Thornvale Group needs a business card design

We need a new business card design using the logo recently selected in a logo competition on Pixel Bazaar. Our business is a consultancy specializing in aviation and energy and the winning business card design will promote an image of precision and professionalism with creativity.

Please use the logo with the name on the front of the card and use a complementary font. Make the back white with either the light grey or dark grey logo.

Target Market(s)

Senior finance and legal leaders at aviation and energy companies

Industry/Entity Type

Management Consulting

Contact Information for Business Card

Peter Castrell
President
Thornvale Group

www.thornvalegroup.example

(555) 204-6391
pc@thornvalegroup.example

Requirements
Must have
• Professional font that goes well with the logo font

```html
<!DOCTYPE html>
<html lang="en">
<head>
<meta charset="utf-8">
<title>Thornvale Group – Business Card</title>
<link href="https://fonts.googleapis.com/css2?family=Open+Sans:wght@300;400;700&display=swap" rel="stylesheet">
<style>
  :root {
    --backdrop: #3b2a1d;
    --card-white: #ffffff;
    --navy: #0f3d68;
    --blue: #1f6e99;
    --blue-deep: #0a2a4a;
    --steel-grey: #9a9ea3;
    --text-grey: #5f6366;
    --name-grey: #4d5054;
  }
  * { margin: 0; padding: 0; box-sizing: border-box; }
  html, body { width: 1200px; height: 913px; overflow: hidden; }
  body {
    background: var(--backdrop);
    font-family: "Open Sans", Arial, sans-serif;
    position: relative;
  }
  .card {
    position: absolute;
    width: 560px;
    height: 320px;
    border-radius: 3px;
    overflow: hidden;
    box-shadow: 0 10px 24px rgba(0,0,0,.35);
  }
  /* Front */
  .card-front { left: 60px; top: 130px; background: var(--card-white); }
  .accent-panel {
    position: absolute; right: 0; top: 0; width: 150px; height: 100%;
    background: linear-gradient(160deg, var(--blue) 0%, var(--navy) 100%);
  }
  .accent-stripe {
    position: absolute; right: 150px; top: 0; width: 14px; height: 100%;
    background: var(--steel-grey);
  }
  .wordmark { position: absolute; left: 36px; top: 70px; display: flex; align-items: center; gap: 12px; }
  .wordmark-square { width: 16px; height: 16px; background: var(--navy); }
  .wordmark-name {
    font-weight: 300; font-size: 30px; letter-spacing: 3px;
    color: var(--navy); line-height: 1.15; text-transform: uppercase;
  }
  .wordmark-name span { display: block; font-size: 14px; letter-spacing: 14px; padding-left: 4px; }
  .contact-block { position: absolute; left: 36px; top: 170px; }
  .person-name { font-weight: 700; font-size: 21px; color: var(--name-grey); }
  .person-title { font-size: 13px; color: var(--navy); margin-bottom: 16px; }
  .contact-list { list-style: none; font-size: 13px; color: var(--text-grey); line-height: 1.6; }
  .contact-list li { display: flex; align-items: center; gap: 8px; }
  .contact-list svg { width: 11px; height: 11px; fill: none; stroke: var(--name-grey); stroke-width: 1.6; }
  /* Back */
  .card-back {
    left: 600px; top: 480px;
    background: linear-gradient(170deg, var(--blue) 0%, var(--navy) 55%, var(--blue-deep) 100%);
    display: flex; align-items: center; justify-content: center;
  }
  .card-back .wordmark { position: static; }
  .card-back .wordmark-square { background: #ffffff; }
  .card-back .wordmark-name { color: #ffffff; font-size: 36px; }
  .card-back .wordmark-name span { font-size: 16px; letter-spacing: 17px; }
</style>
</head>
<body>
  <section class="card card-front" aria-label="Card front">
    <div class="accent-stripe"></div>
    <div class="accent-panel"></div>
    <div class="wordmark">
      <div class="wordmark-square"></div>
      <div class="wordmark-name">Thornvale<span>Group</span></div>
    </div>
    <div class="contact-block">
      <p class="person-name">Peter Castrell</p>
      <p class="person-title">President</p>
      <ul class="contact-list">
        <li><svg viewBox="0 0 12 12"><path d="M2 1.5h2.5l1 2.5-1.5 1a6 6 0 0 0 3 3l1-1.5 2.5 1V10a1 1 0 0 1-1 1A9 9 0 0 1 1 2.5a1 1 0 0 1 1-1z"/></svg>(555) 204-6391</li>
        <li><svg viewBox="0 0 12 12"><rect x="1" y="2.5" width="10" height="7"/><path d="M1 2.5l5 4 5-4"/></svg>pc@thornvalegroup.example</li>
        <li><svg viewBox="0 0 12 12"><circle cx="6" cy="6" r="5"/><path d="M1 6h10M6 1c-3 3-3 7 0 10M6 1c3 3 3 7 0 10"/></svg>www.thornvalegroup.example</li>
      </ul>
    </div>
  </section>

  <section class="card card-back" aria-label="Card back">
    <div class="wordmark">
      <div class="wordmark-square"></div>
      <div class="wordmark-name">Thornvale<span>Group</span></div>
    </div>
  </section>
</body>
</html>
```